Dashboard Elements

Hello – looking for someone to create dashboard elements.
I’ve already basically designed all these elements – but I need someone to take what I’ve designed and make it look like an actual dashboard UI, like an app - assuming using some kind of dashboard UI kit (but however you would like to get it done is fine). It can look just like mine or try something different, as long as it matches the color scheme webpage that I’m going to out it on – see the page here. I’m ok with making it dark, maybe that would look better – again as long as it matches the webpage (https://www.plandeck.io/file/7QxKtr2BwLpZnVe4Hs8Mc1/Webpage-with-placeholders?node-id=0%3A1). Please note, you do not need to put anything on the webpage or do anything with this Figma file, this is just a reference so you can color/stylize it accordingly.

The attached Powerpoint file has everything you need - make sure to zoom all the way out to see everything on the slides.

Here are the Dashboard elements needed (this will all make sense when you look at the PPT):
Dashboard 1
Dashboard 1 – expanded view A
Dashboard 1 – expanded view B
View Source button by itself
Source Document Viewer 1 and 2 (these are exactly the same just with a different image inside)*
Dashboard 2 (only slightly different than Dashboard 1, just extended with extra headings
Table of Contents
Searchbar and Source Doc by itself
*the documents in the source document viewers should still look like documents - they don’t need to look like part of the UI, because this is a document viewer – you can restyle/recolor if necessary or just leave these as is.
- Colors must match color scheme of webpage, attached and on Figma link (images there currently are only placeholders) – ok to go dark as long as it matches
- Must look sleek, clean, realistic
- Don’t add any pictures of people or change the text.
- In case it’s not clear, this is what I mean by the concept of Dashboard UI - https://www.notavia.net/shard/s7/sh/8fad21bc-14e9-4a7c-b2d0-5c3e9f71a604/92c4e1b7a05d3f68e1c2b947d0a3f815
- Must be sent in an editable file, I may need to be edit text and other elements
- If you are going to send a sample, please make sure it’s part of the dashboard itself, not just the table of contents etc

Ideally hoping to find someone I can continue working with as I'll have a lot more graphic design work needed coming up.

Thank you!

```html
<!DOCTYPE html>
<html lang="en">
<head>
<meta charset="utf-8">
<title>Dashboard 2 and Table of Contents</title>
<link rel="stylesheet" href="https://fonts.googleapis.com/css2?family=Catamaran:wght@500;600;700&family=Open+Sans:wght@400;600&display=swap">
<style>
:root{
  --bg-deep:#0f0c20;
  --bg-glow:#3a2a78;
  --panel:#16122e;
  --panel-top:#1f1a3f;
  --card:#15112b;
  --teal:#1cbfb7;
  --teal-soft:#4fd6cf;
  --purple:#7a63e6;
  --purple-light:#a394f5;
  --lavender:#8a80d6;
  --heading:#7b6be6;
  --text:#e9e7f7;
  --muted:#bdb8dc;
  --track:#f4f3fb;
}
*{margin:0;padding:0;box-sizing:border-box}
html,body{width:1200px;height:718px;overflow:hidden}
body{
  position:relative;
  background:
    radial-gradient(ellipse 520px 420px at 0 640px,var(--bg-glow),transparent 70%),
    radial-gradient(ellipse 700px 300px at 500px 718px,#1d1640,transparent 70%),
    var(--bg-deep);
  font-family:"Open Sans",sans-serif;
  color:var(--text);
}
.abs{position:absolute}
.mid{transform:translateY(-50%);line-height:1;white-space:nowrap}
.board-title{
  font-family:"Catamaran",sans-serif;font-weight:700;font-size:36px;
  color:var(--heading);letter-spacing:.5px;transform:translate(-50%,-50%);line-height:1;
}
.panel{overflow:hidden;background:var(--panel)}
.blob{position:absolute;border-radius:50%}
.card{
  border-radius:26px;
  border:3px solid transparent;
  background:
    linear-gradient(var(--card),var(--card)) padding-box,
    linear-gradient(135deg,var(--teal),var(--purple) 55%,var(--teal)) border-box;
}
.brand-mark{width:10px;height:10px;background:var(--teal);border-radius:2px}
.brand-name{font-size:11px;letter-spacing:.6px;color:var(--text);font-weight:400}
.app-title{font-family:"Catamaran",sans-serif;font-weight:600;font-size:23px;color:var(--heading)}
.patient-name{font-size:9px;color:var(--text)}
.patient-meta{font-size:5px;color:var(--muted)}
.section-label{font-size:8.5px;color:var(--text)}
.outline-pill{
  border:1px solid var(--teal);border-radius:8px;color:var(--teal-soft);
  font-size:6px;display:flex;align-items:center;justify-content:center;
}
.stat{font-size:6.5px;color:var(--teal-soft)}
.stat-plain{font-size:6.5px;color:var(--text)}
.count-ring{width:11px;height:11px;border:1px solid var(--purple-light);border-radius:50%;
  font-size:7px;display:flex;align-items:center;justify-content:center;color:var(--text)}
.col-head{font-size:6.5px;color:var(--text);display:flex;align-items:center;gap:3px}
.sort-dot{width:7px;height:7px;border-radius:50%;background:var(--purple);display:inline-flex;align-items:center;justify-content:center}
.col-rule{height:3px;border-radius:2px;background:var(--purple);opacity:.75}
.code{font-size:9px;color:var(--teal-soft)}
.cond{font-size:5px;color:var(--text)}
.cat-pill{height:10px;border-radius:6px;background:var(--purple);border:1px solid var(--purple-light);
  box-shadow:0 0 4px rgba(122,99,230,.6);font-size:5px;color:#fff;display:flex;align-items:center;justify-content:center}
.raf{font-size:8.5px;color:var(--teal-soft)}
.meter{height:9px;border-radius:5px;background:var(--track);overflow:hidden}
.meter-fill{height:100%;background:var(--teal);font-size:4px;color:#fff;display:flex;align-items:center;padding-left:4px}
.chev{width:8px;height:6px}
.toc-head{
  border-radius:22px;border:2px solid #2c5b72;background:#1b1738;
  display:flex;align-items:center;justify-content:center;gap:18px;
  font-family:"Catamaran",sans-serif;font-weight:600;font-size:22px;color:var(--lavender);
}
.toc-active{background:var(--teal)}
.toc-item{font-family:"Catamaran",sans-serif;font-weight:600;font-size:16.5px;color:#fff}
</style>
</head>
<body>
<svg width="0" height="0" class="abs" aria-hidden="true">
  <symbol id="chevron" viewBox="0 0 10 6"><polyline points="1,1 5,5 9,1" fill="none" stroke="currentColor" stroke-width="1.8" stroke-linecap="round" stroke-linejoin="round"/></symbol>
</svg>

<div class="abs board-title" style="left:298px;top:76px">Dashboard 2</div>
<div class="abs board-title" style="left:891px;top:76px">TABLE</div>

<!-- Dashboard panel -->
<section class="abs panel" style="left:42px;top:131px;width:535px;height:549px">
  <div class="blob" style="left:-80px;top:-260px;width:460px;height:360px;background:var(--panel-top)"></div>
  <div class="blob" style="left:-70px;top:272px;width:140px;height:140px;background:var(--teal)"></div>
  <div class="blob" style="left:485px;top:187px;width:140px;height:140px;background:var(--purple)"></div>
  <div class="blob" style="left:490px;top:290px;width:120px;height:120px;background:var(--teal);opacity:.9"></div>
  <div class="blob" style="left:300px;top:470px;width:360px;height:200px;background:radial-gradient(circle,#15534f,transparent 70%)"></div>
</section>
<main class="abs card" style="left:70px;top:154px;width:482px;height:496px"></main>

<header>
  <div class="abs brand-mark" style="left:95px;top:174px"></div>
  <div class="abs mid brand-name" style="left:111px;top:179px">CLINIVAULT</div>
  <div class="abs mid app-title" style="left:215px;top:178px">C-CDA Compendium</div>
  <div class="abs mid patient-name" style="left:439px;top:177px">Patient, Jane</div>
  <span class="abs sort-dot" style="left:497px;top:173px;color:#fff"><svg class="chev" style="width:4px;height:3px"><use href="#chevron"/></svg></span>
  <div class="abs mid patient-meta" style="left:439px;top:190px">Female | 01/11/1951 | Age: 70</div>
  <svg class="abs" style="left:518px;top:170px" width="12" height="13" viewBox="0 0 12 13" aria-label="Notifications"><path d="M6 1.5a3.5 3.5 0 0 0-3.5 3.5v3L1 10h10L9.5 8V5A3.5 3.5 0 0 0 6 1.5z" fill="var(--purple-light)"/><circle cx="6" cy="11.5" r="1.3" fill="var(--purple-light)"/><circle cx="10" cy="2.5" r="2" fill="var(--teal)"/></svg>
</header>

<section class="hcc-summary">
  <svg class="abs chev" style="left:183px;top:211px;color:var(--teal)"><use href="#chevron"/></svg>
  <div class="abs mid section-label" style="left:197px;top:214px">HCC Summary</div>
  <div class="abs outline-pill" style="left:267px;top:207px;width:103px;height:14px">Newly Identified ICD-10 Codes</div>
  <div class="abs mid stat" style="left:387px;top:215px">RAF: 2.362</div>
  <div class="abs mid stat-plain" style="left:426px;top:215px">Condition Count</div>
  <div class="abs count-ring" style="left:478px;top:209px">8</div>
  <div class="abs mid stat" style="left:497px;top:215px">ID: 7326472</div>
</section>

<section class="table-new">
  <div class="abs mid col-head" style="left:197px;top:249px">ICD-10 Code <span class="sort-dot"></span></div>
  <div class="abs mid col-head" style="left:297px;top:249px">Condition <span class="sort-dot"></span></div>
  <div class="abs mid col-head" style="left:408px;top:249px">Catagory <span class="sort-dot"></span></div>
  <div class="abs mid col-head" style="left:486px;top:249px">RAF <span class="sort-dot"></span></div>
  <div class="abs col-rule" style="left:195px;top:259px;width:52px"></div>
  <div class="abs col-rule" style="left:268px;top:259px;width:74px"></div>
  <div class="abs col-rule" style="left:402px;top:259px;width:51px"></div>
  <div class="abs col-rule" style="left:482px;top:259px;width:40px"></div>

  <div class="abs mid code" style="left:198px;top:278px">170.0</div>
  <div class="abs mid cond" style="left:270px;top:277px">Aortic Atherosclerosis</div>
  <div class="abs cat-pill" style="left:402px;top:272px;width:50px">108</div>
  <div class="abs mid raf" style="left:484px;top:278px">0.298</div>
  <svg class="abs chev" style="left:514px;top:275px;color:#fff"><use href="#chevron"/></svg>

  <div class="abs mid code" style="left:198px;top:303px">F33.1</div>
  <div class="abs mid cond" style="left:270px;top:302px">Major depressive disorder, recurrent, mild</div>
  <div class="abs cat-pill" style="left:402px;top:297px;width:50px">58</div>
  <div class="abs mid raf" style="left:484px;top:303px">0.309</div>
  <svg class="abs chev" style="left:514px;top:300px;color:#fff"><use href="#chevron"/></svg>

  <div class="abs mid code" style="left:198px;top:329px">148.2</div>
  <div class="abs mid cond" style="left:270px;top:328px">Cronic Artial Fibrillation</div>
  <div class="abs cat-pill" style="left:402px;top:323px;width:50px">96</div>
  <div class="abs mid raf" style="left:484px;top:329px">0.268</div>
  <svg class="abs chev" style="left:514px;top:326px;color:#fff"><use href="#chevron"/></svg>

  <div class="abs mid code" style="left:198px;top:355px">120.9</div>
  <div class="abs mid cond" style="left:270px;top:353px">Angina Pectoris</div>
  <div class="abs cat-pill" style="left:402px;top:348px;width:50px">88</div>
  <div class="abs mid raf" style="left:484px;top:355px">.14</div>
  <svg class="abs chev" style="left:514px;top:351px;color:#fff"><use href="#chevron"/></svg>
</section>

<section class="table-known">
  <div class="abs outline-pill" style="left:262px;top:379px;width:113px;height:14px">Previously Known ICD-10 Codes</div>
  <div class="abs mid col-head" style="left:197px;top:415px">ICD-10 Code <span class="sort-dot"></span></div>
  <div class="abs mid col-head" style="left:297px;top:415px">Condition <span class="sort-dot"></span></div>
  <div class="abs mid col-head" style="left:408px;top:415px">Catagory <span class="sort-dot"></span></div>
  <div class="abs mid col-head" style="left:486px;top:415px">RAF <span class="sort-dot"></span></div>
  <div class="abs col-rule" style="left:195px;top:425px;width:52px"></div>
  <div class="abs col-rule" style="left:268px;top:425px;width:74px"></div>
  <div class="abs col-rule" style="left:402px;top:425px;width:51px"></div>
  <div class="abs col-rule" style="left:482px;top:425px;width:40px"></div>

  <div class="abs mid code" style="left:198px;top:444px">F32.9</div>
  <div class="abs mid cond" style="left:261px;top:442px">Major Depressive Disorder, Single Episode, Unspecified</div>
  <div class="abs cat-pill" style="left:402px;top:437px;width:50px">n/a</div>
  <div class="abs mid raf" style="left:484px;top:444px">0</div>
  <svg class="abs chev" style="left:514px;top:441px;color:#fff"><use href="#chevron"/></svg>

  <div class="abs mid code" style="left:198px;top:470px">Z79.01</div>
  <div class="abs mid cond" style="left:261px;top:468px">Long-term use of anticoagulants</div>
  <div class="abs cat-pill" style="left:402px;top:463px;width:50px">n/a</div>
  <div class="abs mid raf" style="left:484px;top:470px">0</div>
  <svg class="abs chev" style="left:514px;top:466px;color:#fff"><use href="#chevron"/></svg>

  <div class="abs mid code" style="left:198px;top:496px">125.9</div>
  <div class="abs mid cond" style="left:261px;top:494px">Chronic ischemic heart disease, unspecified</div>
  <div class="abs cat-pill" style="left:402px;top:489px;width:50px">n/a</div>
  <div class="abs mid raf" style="left:484px;top:496px">0</div>
  <svg class="abs chev" style="left:514px;top:492px;color:#fff"><use href="#chevron"/></svg>

  <div class="abs mid code" style="left:198px;top:521px">D45</div>
  <div class="abs mid cond" style="left:261px;top:520px">Polycythemia vera</div>
  <div class="abs cat-pill" style="left:402px;top:514px;width:50px">48</div>
  <div class="abs mid raf" style="left:484px;top:521px">0.312</div>
  <svg class="abs chev" style="left:514px;top:518px;color:#fff"><use href="#chevron"/></svg>
</section>

<section class="table-cohort">
  <div class="abs mid col-head" style="left:91px;top:559px">ICD-10 Code <span class="sort-dot"></span></div>
  <div class="abs mid col-head" style="left:179px;top:559px">Condition <span class="sort-dot"></span></div>
  <div class="abs mid col-head" style="left:250px;top:559px">Catagory <span class="sort-dot"></span></div>
  <div class="abs mid col-head" style="left:314px;top:559px">Predicted <span class="sort-dot"></span></div>
  <div class="abs mid col-head" style="left:370px;top:559px">Cohort <span class="sort-dot"></span></div>
  <div class="abs mid col-head" style="left:420px;top:559px">Difference <span class="sort-dot"></span></div>
  <div class="abs mid col-head" style="left:485px;top:559px">Change <span class="sort-dot"></span></div>
  <div class="abs col-rule" style="left:90px;top:569px;width:52px"></div>
  <div class="abs col-rule" style="left:172px;top:569px;width:52px"></div>
  <div class="abs col-rule" style="left:244px;top:569px;width:52px"></div>
  <div class="abs col-rule" style="left:310px;top:569px;width:46px"></div>
  <div class="abs col-rule" style="left:366px;top:569px;width:40px"></div>
  <div class="abs col-rule" style="left:417px;top:569px;width:48px"></div>
  <div class="abs col-rule" style="left:481px;top:569px;width:40px"></div>

  <div class="abs mid code" style="left:93px;top:588px">F32.9</div>
  <div class="abs mid cond" style="left:166px;top:587px">Hypertensive heart disease</div>
  <div class="abs cat-pill" style="left:244px;top:581px;width:51px">50.2</div>
  <div class="abs meter" style="left:311px;top:582px;width:39px"><div class="meter-fill" style="width:62%">72.7%</div></div>
  <div class="abs meter" style="left:366px;top:582px;width:39px"><div class="meter-fill" style="width:45%">22.5%</div></div>
  <div class="abs meter" style="left:418px;top:582px;width:38px"><div class="meter-fill" style="width:62%">72.7%</div></div>
  <div class="abs mid raf" style="left:486px;top:588px">3.23</div>

  <div class="abs mid code" style="left:93px;top:614px">I20.9</div>
  <div class="abs mid cond" style="left:166px;top:612px">Type 2 diabetes mellitus</div>
  <div class="abs cat-pill" style="left:244px;top:607px;width:51px">3.4</div>
  <div class="abs meter" style="left:311px;top:608px;width:39px"><div class="meter-fill" style="width:60%">56.8%</div></div>
  <div class="abs meter" style="left:366px;top:608px;width:39px"><div class="meter-fill" style="width:55%">53.4</div></div>
  <div class="abs meter" style="left:418px;top:608px;width:38px"><div class="meter-fill" style="width:60%">56.8%</div></div>
  <div class="abs mid raf" style="left:486px;top:614px">1.06</div>
</section>

<!-- Table of contents panel -->
<section class="abs panel" style="left:698px;top:132px;width:385px;height:551px">
  <div class="blob" style="left:-40px;top:-250px;width:400px;height:330px;background:var(--panel-top)"></div>
  <div class="blob" style="left:-70px;top:275px;width:140px;height:140px;background:var(--teal)"></div>
  <div class="blob" style="left:300px;top:187px;width:150px;height:150px;background:var(--purple)"></div>
  <div class="blob" style="left:310px;top:290px;width:120px;height:120px;background:var(--teal)"></div>
  <div class="blob" style="left:120px;top:460px;width:360px;height:200px;background:radial-gradient(circle,#15534f,transparent 70%)"></div>
</section>
<nav class="abs card" style="left:738px;top:165px;width:306px;height:486px;overflow:hidden">
  <div class="abs toc-head" style="left:10px;top:7px;width:282px;height:43px">Table of Contents
    <svg style="width:16px;height:11px;color:var(--teal)"><use href="#chevron"/></svg></div>
  <div class="abs toc-active" style="left:0;top:88px;width:306px;height:35px"></div>
  <div class="abs mid toc-item" style="left:19px;top:106px">Insurance Providers</div>
  <div class="abs mid toc-item" style="left:19px;top:143px">Problems</div>
  <div class="abs mid toc-item" style="left:19px;top:180px">Results</div>
  <div class="abs mid toc-item" style="left:19px;top:217px">Procedures</div>
  <div class="abs mid toc-item" style="left:19px;top:254px">Encounters</div>
  <div class="abs mid toc-item" style="left:19px;top:291px">Medications</div>
  <div class="abs mid toc-item" style="left:19px;top:328px">Vital Signs</div>
  <div class="abs mid toc-item" style="left:19px;top:365px">Immunizations</div>
  <div class="abs mid toc-item" style="left:19px;top:401px">Social History</div>
  <div class="abs mid toc-item" style="left:19px;top:438px">Family History</div>
</nav>
</body>
</html>
```